Business Card Design for Software Development Company

I am looking for a business card design the incorporates my new logo (attached below).

Key information to include:
Name: Martin Quelbrook
Title: CEO
Email: martin@brightwellcivic.example
Phone: 555-218-9403
Website: www.brightwellcivic.example

NOTE: This design should be easy to edit so that we can order cards for different members of our team.

```html
<!DOCTYPE html>
<html lang="en">
<head>
<meta charset="utf-8">
<title>Brightwell Business Card</title>
<link href="https://fonts.googleapis.com/css2?family=Montserrat:wght@400;600&display=swap" rel="stylesheet">
<style>
  :root {
    --backdrop: #e4e2e3;
    --paper: #ffffff;
    --slate: #6f7a9b;
    --slate-band: #6b7390;
    --orange: #e8803a;
    --ink: #23242b;
    --navy: #3b3f57;
  }
  * { margin: 0; padding: 0; box-sizing: border-box; }
  html, body {
    width: 1200px; height: 1108px; overflow: hidden;
    background: var(--backdrop);
    font-family: "Montserrat", Arial, sans-serif;
  }
  .canvas { position: relative; width: 1200px; height: 1108px; }

  .card { position: absolute; width: 767px; }
  .card-front { left: 232px; top: 57px; height: 468px; background: var(--paper); }
  .card-back { left: 231px; top: 584px; height: 450px; background: var(--slate); }

  .brand-row { display: flex; align-items: center; }
  .brand-dot { border-radius: 50%; background: var(--orange); flex: none; }
  .brand-name { font-weight: 600; white-space: nowrap; }

  /* Front: brand */
  .front-brand { position: absolute; left: 92px; top: 240px; gap: 10px; }
  .front-brand .brand-dot { width: 26px; height: 26px; }
  .front-brand .brand-name { font-size: 28px; color: var(--navy); line-height: 36px; }

  /* Front: contact */
  .divider { position: absolute; left: 379px; top: 180px; width: 1.5px; height: 149px; background: var(--orange); }
  .contact { position: absolute; left: 393px; top: 180px; }
  .person-name { font-size: 29px; font-weight: 600; color: var(--orange); line-height: 36px; }
  .person-title { font-size: 17px; color: var(--ink); line-height: 22px; margin-top: 0; }
  .contact-list { list-style: none; margin-top: 4px; }
  .contact-list li {
    display: flex; align-items: center; gap: 8px;
    font-size: 18px; color: var(--ink); line-height: 30px;
  }
  .contact-list svg { width: 16px; height: 16px; flex: none; }

  .band { position: absolute; left: 0; bottom: 0; width: 767px; height: 25px; }

  /* Back */
  .back-brand { position: absolute; left: 0; top: 0; width: 767px; height: 450px; justify-content: center; gap: 20px; }
  .back-brand .brand-dot { width: 56px; height: 56px; }
  .back-brand .brand-name { font-size: 66px; color: var(--paper); line-height: 80px; }
</style>
</head>
<body>
<div class="canvas">

  <section class="card card-front">
    <div class="brand-row front-brand">
      <span class="brand-dot"></span>
      <span class="brand-name">Brightwell</span>
    </div>

    <div class="divider"></div>

    <div class="contact">
      <div class="person-name">Martin Quelbrook</div>
      <div class="person-title">CEO</div>
      <ul class="contact-list">
        <li>
          <svg viewBox="0 0 16 16" aria-hidden="true"><path d="M4 1.5l2.2 3-1.3 1.6c.8 1.8 2.2 3.2 4 4l1.6-1.3 3 2.2-1.2 2.4C7.5 13.4 2.6 8.5 1.6 3.7z" fill="var(--orange)"/></svg>
          <span>555-218-9403</span>
        </li>
        <li>
          <svg viewBox="0 0 16 16" aria-hidden="true"><rect x="1.5" y="3.5" width="13" height="9" fill="var(--orange)"/><path d="M1.5 3.5L8 8.5l6.5-5" fill="none" stroke="#fff" stroke-width="1.2"/></svg>
          <span>martin@brightwellcivic.example</span>
        </li>
        <li>
          <svg viewBox="0 0 16 16" aria-hidden="true"><circle cx="8" cy="8" r="7" fill="var(--orange)"/><path d="M1 8h14M8 1c2.5 2.5 2.5 11.5 0 14M8 1c-2.5 2.5-2.5 11.5 0 14" fill="none" stroke="#fff" stroke-width="1"/></svg>
          <span>www.brightwellcivic.example</span>
        </li>
      </ul>
    </div>

    <svg class="band" viewBox="0 0 767 25" aria-hidden="true">
      <polygon points="0,0 392,0 376,25 0,25" fill="var(--slate-band)"/>
      <polygon points="404,0 767,0 767,25 389,25" fill="var(--orange)"/>
    </svg>
  </section>

  <section class="card card-back">
    <div class="brand-row back-brand">
      <span class="brand-dot"></span>
      <span class="brand-name">Brightwell</span>
    </div>
  </section>

</div>
</body>
</html>
```